WebApp for IoT (Vexa lights and Kirra/Brelline)

I am going to create my own dashbord for Quillet Pro (See other examples on https://quillet.example/) But I want it much more flexible and advanced.
One page per room (So I can have an Zanbo in each room with all functions just for that room) and include controls for light (both overall for the room and in an popupwindow all lightbulbs n the room - se more about how its done in Torvald Vexa app on https://www.torvald-vexa.example/en-us/explore-vexa/apps/bridge) aswell as set volume/track for Kirra.

I want the final solution to be "skinable" so I can choose from Blue-CSS to Green-CSS etc, but at this moment I only want ONE color!

I have added an PDF with the functions I am thinking of, but the design is for you to create!

Please have in mind it will be running on Zanbos on the wall, and in the mobile.

For the moment I only want an PSD of the "Room page", "Light popup" and "Sound Popup", but I might contract the winner to get HTML/CSS as second step.

```html
<!DOCTYPE html>
<html lang="en">
<head>
<meta charset="utf-8">
<title>Room Dashboard – Kitchen &amp; Bedroom</title>
<link href="https://fonts.googleapis.com/css2?family=Roboto:wght@500;700&display=swap" rel="stylesheet">
<style>
  :root {
    --page-bg: #8f8f8f;
    --screen-bg: #566660;
    --pill-bg: #ffffff;
    --pill-text: #4e5b57;
    --knob: #4f5f5a;
    --ring: #9aa39f;
    --accent-teal: #5db4bd;
    --star: #f5c400;
    --slider-top: #6e6e6e;
    --slider-bottom: #c9c9c9;
  }
  * { box-sizing: border-box; margin: 0; padding: 0; }
  html, body { width: 849px; height: 1200px; overflow: hidden; }
  body {
    background: var(--page-bg);
    font-family: "Roboto", Arial, sans-serif;
    position: relative;
  }
  .screen {
    position: absolute;
    left: 116px;
    width: 617px;
    height: 404px;
    background: var(--screen-bg);
    border-radius: 8px;
    overflow: hidden;
  }
  .screen--kitchen { top: 141px; }
  .screen--bedroom { top: 655px; }

  .room-scene { position: absolute; left: 0; top: 0; }

  .temperature {
    position: absolute;
    width: 76px; height: 76px;
    border-radius: 50%;
    background: #fff;
    border: 6px solid var(--ring);
    display: flex; align-items: center; justify-content: center;
    font-weight: 700; font-size: 23px; color: var(--pill-text);
  }
  .temperature sup { font-size: 12px; margin-left: 1px; position: relative; top: -3px; }

  .pill {
    position: absolute;
    height: 39px;
    border-radius: 20px;
    background: var(--pill-bg);
    color: var(--pill-text);
    font-weight: 700;
    display: flex; align-items: center; justify-content: center;
    font-size: 18px;
    box-shadow: 0 1px 3px rgba(0,0,0,.25);
  }
  .pill--active { background: var(--accent-teal); color: #fff; }

  .toggle {
    position: absolute;
    height: 39px;
    border-radius: 20px;
    background: var(--pill-bg);
    color: var(--pill-text);
    font-weight: 700;
    font-size: 10.5px;
    display: flex; align-items: center;
    padding-left: 13px;
    box-shadow: 0 1px 3px rgba(0,0,0,.25);
  }
  .toggle::after {
    content: "";
    position: absolute;
    right: 4px; top: 6px;
    width: 27px; height: 27px;
    border-radius: 50%;
    background: var(--knob);
  }
  .toggle--light { left: 498px; width: 87px; }
  .toggle--volume { left: 482px; width: 105px; padding-left: 19px; }

  .star { position: absolute; width: 19px; height: 19px; }

  .slider {
    position: absolute;
    border-radius: 14px;
    background: linear-gradient(var(--slider-top), var(--slider-bottom) 55%, var(--slider-top));
    border: 1px solid #444;
    box-shadow: 0 1px 4px rgba(0,0,0,.35);
  }
  .slider__handle {
    position: absolute; left: 50%; transform: translateX(-50%);
    border-radius: 50%; border: 1.5px solid #eee;
  }
  .slider__label {
    position: absolute;
    background: #3f4a47; color: #fff;
    font-size: 5.5px; font-weight: 700; letter-spacing: .5px;
    border-radius: 4px; padding: 1px 4px;
    transform: translateX(-50%);
  }
  .slider__icon { position: absolute; left: 50%; transform: translateX(-50%); }

  .clock { position: absolute; width: 74px; height: 74px; }
</style>
</head>
<body>

<section class="screen screen--kitchen" aria-label="Kitchen room page">
  <svg class="room-scene" width="617" height="404" role="img" aria-label="Isometric kitchen illustration with dark green cabinets, white counters and bar stools">
    <defs>
      <linearGradient id="kitchen-tone" x1="0" y1="0" x2="1" y2="1">
        <stop offset="0" stop-color="#b9bcb6"/>
        <stop offset="0.55" stop-color="#a7ada8"/>
        <stop offset="1" stop-color="#6d7c76"/>
      </linearGradient>
    </defs>
    <polygon points="309,10 498,119 498,296 309,404 117,298 117,118" fill="url(#kitchen-tone)"/>
  </svg>

  <div class="temperature" style="left:38px;top:3px;">23<sup>0</sup></div>
  <div class="pill" style="left:26px;top:107px;width:99px;">LIGHT</div>

  <svg class="star" style="left:30px;top:164px;" viewBox="0 0 24 24" aria-hidden="true"><polygon points="12,1 15,9 23,9 16.5,14 19,22 12,17 5,22 7.5,14 1,9 9,9" fill="var(--star)" stroke="#8a6d00" stroke-width=".8"/></svg>
  <span class="slider__label" style="left:76px;top:168px;">100%</span>
  <div class="slider" style="left:56px;top:181px;width:40px;height:110px;">
    <span class="slider__handle" style="top:4px;width:26px;height:26px;"></span>
    <svg class="slider__icon" style="top:88px;" width="14" height="14" viewBox="0 0 14 14" aria-hidden="true">
      <circle cx="7" cy="7" r="2.6" fill="#fff"/>
      <g stroke="#fff" stroke-width="1.2"><line x1="7" y1="0.5" x2="7" y2="2.5"/><line x1="7" y1="11.5" x2="7" y2="13.5"/><line x1="0.5" y1="7" x2="2.5" y2="7"/><line x1="11.5" y1="7" x2="13.5" y2="7"/><line x1="2.4" y1="2.4" x2="3.8" y2="3.8"/><line x1="10.2" y1="10.2" x2="11.6" y2="11.6"/><line x1="2.4" y1="11.6" x2="3.8" y2="10.2"/><line x1="10.2" y1="3.8" x2="11.6" y2="2.4"/></g>
    </svg>
  </div>

  <svg class="clock" style="left:489px;top:-1px;" viewBox="0 0 74 74" aria-label="Clock">
    <circle cx="37" cy="37" r="36" fill="#fff" stroke="#111" stroke-width="1.5"/>
    <circle cx="37" cy="37" r="30" fill="none" stroke="#111" stroke-width=".6"/>
    <g stroke="#111" stroke-width="2.2">
      <line x1="37" y1="3" x2="37" y2="10"/><line x1="37" y1="64" x2="37" y2="71"/><line x1="3" y1="37" x2="10" y2="37"/><line x1="64" y1="37" x2="71" y2="37"/>
      <line x1="54" y1="7.6" x2="50.5" y2="13.6"/><line x1="66.4" y1="20" x2="60.4" y2="23.5"/><line x1="66.4" y1="54" x2="60.4" y2="50.5"/><line x1="54" y1="66.4" x2="50.5" y2="60.4"/><line x1="20" y1="66.4" x2="23.5" y2="60.4"/><line x1="7.6" y1="54" x2="13.6" y2="50.5"/><line x1="7.6" y1="20" x2="13.6" y2="23.5"/><line x1="20" y1="7.6" x2="23.5" y2="13.6"/>
    </g>
    <line x1="37" y1="37" x2="50" y2="52" stroke="#111" stroke-width="2.4"/>
    <line x1="37" y1="37" x2="57" y2="43" stroke="#111" stroke-width="1.6"/>
    <line x1="37" y1="37" x2="30" y2="32" stroke="#111" stroke-width="1.6"/>
    <circle cx="37" cy="37" r="2" fill="#111"/>
  </svg>

  <div class="toggle toggle--light" style="top:106px;">LIGHT 1</div>
  <div class="toggle toggle--light" style="top:164px;">LIGHT 2</div>
  <div class="toggle toggle--light" style="top:221px;">LIGHT 3</div>
</section>

<section class="screen screen--bedroom" aria-label="Bedroom room page">
  <svg class="room-scene" width="617" height="404" role="img" aria-label="Isometric bedroom illustration with teal bed, curtains, TV and armchair">
    <defs>
      <linearGradient id="bedroom-tone" x1="0" y1="0" x2="1" y2="1">
        <stop offset="0" stop-color="#8fa89e"/>
        <stop offset="0.5" stop-color="#8fb2b2"/>
        <stop offset="1" stop-color="#b9b2a7"/>
      </linearGradient>
    </defs>
    <polygon points="306,16 470,108 470,285 320,400 170,300 170,108" fill="url(#bedroom-tone)"/>
  </svg>

  <div class="temperature" style="left:38px;top:9px;">21<sup>0</sup></div>
  <div class="pill" style="left:26px;top:112px;width:99px;">LIGHT</div>
  <div class="pill pill--active" style="left:26px;top:160px;width:99px;font-size:17px;">VOLUME</div>
  <svg class="star" style="left:22px;top:121px;" viewBox="0 0 24 24" aria-hidden="true"><polygon points="12,1 15,9 23,9 16.5,14 19,22 12,17 5,22 7.5,14 1,9 9,9" fill="var(--star)" stroke="#8a6d00" stroke-width=".8"/></svg>
  <svg class="star" style="left:22px;top:169px;" viewBox="0 0 24 24" aria-hidden="true"><polygon points="12,1 15,9 23,9 16.5,14 19,22 12,17 5,22 7.5,14 1,9 9,9" fill="var(--star)" stroke="#8a6d00" stroke-width=".8"/></svg>

  <span class="slider__label" style="left:145px;top:85px;font-size:4.5px;">100%</span>
  <div class="slider" style="left:131px;top:93px;width:28px;height:75px;">
    <span class="slider__handle" style="top:3px;width:17px;height:17px;"></span>
    <svg class="slider__icon" style="top:57px;" width="14" height="11" viewBox="0 0 14 11" aria-hidden="true">
      <polygon points="0,3.5 3,3.5 6.5,0.5 6.5,10.5 3,7.5 0,7.5" fill="#fff"/>
      <path d="M8.5 3.2 Q10 5.5 8.5 7.8 M10.3 1.8 Q12.8 5.5 10.3 9.2" fill="none" stroke="#fff" stroke-width="1.1"/>
    </svg>
  </div>

  <svg class="clock" style="left:490px;top:5px;" viewBox="0 0 74 74" aria-label="Clock">
    <circle cx="37" cy="37" r="36" fill="#fff" stroke="#111" stroke-width="1.5"/>
    <circle cx="37" cy="37" r="30" fill="none" stroke="#111" stroke-width=".6"/>
    <g stroke="#111" stroke-width="2.2">
      <line x1="37" y1="3" x2="37" y2="10"/><line x1="37" y1="64" x2="37" y2="71"/><line x1="3" y1="37" x2="10" y2="37"/><line x1="64" y1="37" x2="71" y2="37"/>
      <line x1="54" y1="7.6" x2="50.5" y2="13.6"/><line x1="66.4" y1="20" x2="60.4" y2="23.5"/><line x1="66.4" y1="54" x2="60.4" y2="50.5"/><line x1="54" y1="66.4" x2="50.5" y2="60.4"/><line x1="20" y1="66.4" x2="23.5" y2="60.4"/><line x1="7.6" y1="54" x2="13.6" y2="50.5"/><line x1="7.6" y1="20" x2="13.6" y2="23.5"/><line x1="20" y1="7.6" x2="23.5" y2="13.6"/>
    </g>
    <line x1="37" y1="37" x2="50" y2="52" stroke="#111" stroke-width="2.4"/>
    <line x1="37" y1="37" x2="57" y2="43" stroke="#111" stroke-width="1.6"/>
    <line x1="37" y1="37" x2="30" y2="32" stroke="#111" stroke-width="1.6"/>
    <circle cx="37" cy="37" r="2" fill="#111"/>
  </svg>

  <div class="toggle toggle--volume" style="top:112px;">VOLUME 1</div>
  <div class="toggle toggle--volume" style="top:160px;">VOLUME 2</div>
  <div class="toggle toggle--volume" style="top:208px;">VOLUME 3</div>
  <div class="toggle toggle--volume" style="top:255px;">VOLUME 4</div>
</section>

</body>
</html>
```